Brindle Yard Care. The best in the biz

I run a lawn care service that offers full service mowing. 100% satisfaction guarantee. Fast, Friendly, quality service "I am your lawns best friend" I cut residential lawns. I offer a mow package that includes trimming, edging and clean up. Prices very from 20 dollars to 75. I want my logo to stand out. Free estimates

Target Market(s)

Home owners

Industry/Entity Type

Landscaping

Contact Information for Business Card

555-812-4473 tomvale48@quillmail.net Derek. Brindle Yard care

Colors
f37122
9bcb3c
cadf82

Requirements
Must have
• Company name.
• Phone number
• Email
• My services
• images
Nice to have
• A sun that is growing grass.
Should not have
• Incorrect information

```html
<!DOCTYPE html>
<html lang="en">
<head>
<meta charset="utf-8">
<title>Brindle Yard Care – Business Card</title>
<link rel="stylesheet" href="https://fonts.googleapis.com/css2?family=Open+Sans:wght@400;600;700&display=swap">
<style>
  :root {
    --green: #9bcb3c;
    --green-light: #cadf82;
    --orange: #f37122;
    --charcoal: #3d3d3d;
    --ink: #222222;
    --black: #0c0c0c;
    --white: #ffffff;
    --backdrop: #e8e5e0;
  }
  * { box-sizing: border-box; margin: 0; padding: 0; }
  html, body {
    width: 1200px;
    height: 900px;
    overflow: hidden;
    background: var(--backdrop);
    font-family: "Open Sans", Arial, sans-serif;
  }
  .sheet {
    position: relative;
    width: 1200px;
    height: 900px;
  }
  .card {
    position: absolute;
    left: 250px;
    width: 700px;
    height: 400px;
    overflow: hidden;
    box-shadow: 0 6px 18px rgba(0,0,0,0.18);
  }
  /* Back side */
  .card--back {
    top: 35px;
    background: var(--black);
    color: var(--white);
  }
  .card--back .brand-dot {
    position: absolute;
    left: 320px;
    top: 70px;
    width: 90px;
    height: 90px;
    border-radius: 50%;
    background: var(--green);
  }
  .card--back .brand-name {
    position: absolute;
    left: 0;
    right: 0;
    top: 172px;
    text-align: center;
    font-size: 42px;
    font-weight: 400;
    letter-spacing: 0.5px;
  }
  .card--back .taglines {
    position: absolute;
    left: 0;
    right: 0;
    top: 240px;
    text-align: center;
    list-style: none;
    font-size: 19px;
    font-weight: 600;
    line-height: 30px;
  }
  /* Front side */
  .card--front {
    top: 465px;
    background: var(--white);
  }
  .card--front .shapes {
    position: absolute;
    inset: 0;
  }
  .card--front .owner {
    position: absolute;
    left: 92px;
    top: 30px;
    color: var(--green);
    font-size: 19px;
    font-weight: 700;
  }
  .card--front .contact {
    position: absolute;
    left: 28px;
    top: 220px;
    list-style: none;
    color: var(--ink);
    font-size: 17px;
    line-height: 27px;
  }
  .card--front .contact li {
    display: flex;
    align-items: center;
    gap: 10px;
  }
  .card--front .contact svg {
    width: 13px;
    height: 13px;
    flex: none;
  }
  .card--front .brand-dot {
    position: absolute;
    left: 470px;
    top: 110px;
    width: 104px;
    height: 104px;
    border-radius: 50%;
    background: var(--green);
  }
  .card--front .brand-name {
    position: absolute;
    left: 255px;
    top: 228px;
    color: var(--green);
    font-size: 40px;
    font-weight: 400;
    white-space: nowrap;
  }
</style>
</head>
<body>
<main class="sheet">

  <section class="card card--back" aria-label="Business card, back">
    <div class="brand-dot" aria-hidden="true"></div>
    <h1 class="brand-name">Brindle Yard Care</h1>
    <ul class="taglines">
      <li>100% satisfaction guarantee.</li>
      <li>Fast, Friendly, Quality Service</li>
      <li>I am your lawns best friend</li>
    </ul>
  </section>

  <section class="card card--front" aria-label="Business card, front">
    <svg class="shapes" viewBox="0 0 700 400" aria-hidden="true">
      <polygon points="0,0 8,0 8,40 0,40" fill="var(--green)"/>
      <polygon points="40,0 80,0 68,48 14,48" fill="var(--charcoal)"/>
      <polygon points="0,302 250,302 232,338 0,338" fill="var(--green)"/>
      <polygon points="262,346 700,346 700,400 240,400" fill="var(--charcoal)"/>
    </svg>

    <p class="owner">Derek</p>

    <ul class="contact">
      <li>
        <svg viewBox="0 0 24 24"><path fill="var(--green)" d="M6.6 10.8a15.1 15.1 0 0 0 6.6 6.6l2.2-2.2a1 1 0 0 1 1-.25 11.4 11.4 0 0 0 3.6.57 1 1 0 0 1 1 1V20a1 1 0 0 1-1 1A17 17 0 0 1 3 4a1 1 0 0 1 1-1h3.5a1 1 0 0 1 1 1c0 1.25.2 2.45.57 3.57a1 1 0 0 1-.25 1z"/></svg>
        555-812-4473
      </li>
      <li>
        <svg viewBox="0 0 24 24"><rect x="2" y="5" width="20" height="14" rx="2" fill="var(--green)"/><path d="M3 7l9 6 9-6" fill="none" stroke="var(--white)" stroke-width="2"/></svg>
        tomvale48@quillmail.net
      </li>
    </ul>

    <div class="brand-dot" aria-hidden="true"></div>
    <h2 class="brand-name">Brindle Yard Care</h2>
  </section>

</main>
</body>
</html>
```